Additional Benefits of Working for VELMAR

Please prepare an infographic on the additional benefits besides salary of working at VELMAR as detailed in the attached word document. Also attached is our logo in eps and our company design "Grounds". We are a Not For Profit company that finds jobs for unemployed people of government benefit payments

Target Market(s)

Attracting people to work for VELMAR. Making VELMAR an employer of choice.

Font styles to use
Sans Serif

Colors

Designer to choose colors to be used in the design.

Requirements
Must have
• be on 1 page
• have our logo
Nice to have
• Our Grounds design worked into it.
• Happy engaged employees
• Community engagement - we are a not for profit organisation
Should not have
• Discrimination, swearing,

```html
<!DOCTYPE html>
<html lang="en">
<head>
<meta charset="utf-8">
<title>The Benefits of Working with Us – VELMAR</title>
<link href="https://fonts.googleapis.com/css2?family=Quicksand:wght@400;500;600;700&display=swap" rel="stylesheet">
<style>
  :root {
    --green-dark: #0f6e5c;
    --green: #1a9379;
    --green-light: #2fb08f;
    --gold: #c98a2e;
    --gold-light: #e0a851;
    --gold-dark: #a86c1c;
    --ink: #1d1d1d;
    --paper: #ffffff;
    --ground-grey: #8f9593;
    --ground-mint: #a9cdb8;
    --ground-peach: #e8c39b;
  }
  * { box-sizing: border-box; margin: 0; padding: 0; }
  html, body { width: 1200px; height: 1096px; overflow: hidden; background: var(--paper); }
  body { font-family: "Quicksand", sans-serif; color: var(--ink); }

  .sheet {
    position: absolute; left: 16px; top: 2px;
    width: 840px; height: 785px;
    transform: scale(1.39); transform-origin: 0 0;
  }
  .connectors { position: absolute; inset: 0; width: 840px; height: 785px; }

  .title-banner {
    position: absolute; left: 246px; top: 15px; width: 574px; height: 67px;
    border-radius: 22px;
    background: linear-gradient(180deg, var(--green-light), var(--green-dark));
    color: #fff; font-size: 33px; font-weight: 500;
    display: flex; align-items: center; justify-content: center; letter-spacing: 0.2px;
  }
  .brand {
    position: absolute; left: 30px; top: 64px;
    font-size: 40px; font-weight: 700; color: var(--ink); letter-spacing: -1px;
  }

  .card {
    position: absolute; width: 180px;
    border: 4px solid var(--gold); border-radius: 18px; overflow: hidden;
    background: var(--ground-grey);
  }
  .card-head {
    position: relative; z-index: 1;
    background: linear-gradient(180deg, var(--gold-light), var(--gold));
    color: #fff; text-align: center; font-size: 15px; font-weight: 500; line-height: 20px;
    padding: 3px 4px 5px;
  }
  .card-ground {
    position: absolute; inset: 0;
    background: linear-gradient(135deg, var(--ground-grey) 0%, var(--ground-mint) 45%, var(--ground-grey) 70%, var(--ground-peach) 100%);
  }
  .card-list { position: relative; z-index: 1; list-style: none; padding: 4px 4px 5px 5px; }
  .card-list li { font-size: 8.4px; line-height: 16.5px; letter-spacing: -0.1px; }
  .card-list li::before { content: "• "; }

  .icon-ring {
    position: absolute; width: 104px; height: 104px; border-radius: 50%;
    border: 4px solid var(--green); background: #fff;
    display: flex; align-items: center; justify-content: center;
  }
  .icon-ring svg { width: 54px; height: 54px; stroke: var(--green); fill: none; stroke-width: 3; stroke-linecap: round; stroke-linejoin: round; }
</style>
</head>
<body>
<div class="sheet">
  <svg class="connectors" viewBox="0 0 840 785" aria-hidden="true">
    <g stroke="#1a9379" stroke-width="4" fill="none">
      <path d="M298 220V262"/>
      <path d="M348 155H417"/>
      <path d="M593 150H655"/>
      <path d="M705 225V262"/>
      <path d="M96 415V450"/>
      <path d="M158 470H218"/>
      <path d="M108 548V587"/>
      <path d="M394 435H446"/>
      <path d="M546 427H617"/>
      <path d="M490 346V385"/>
      <path d="M524 485V529"/>
      <path d="M326 493V525"/>
      <path d="M506 645V660"/>
      <path d="M556 735H700Q725 735 725 710V690"/>
    </g>
  </svg>

  <div class="title-banner">The Benefits of Working with Us</div>
  <div class="brand">VELMAR</div>

  <div class="icon-ring" style="left:246px;top:116px" aria-label="Wellbeing icon">
    <svg viewBox="0 0 54 54"><path d="M27 46 8 27C2 21 4 11 12 9c6-1 11 2 15 7 4-5 9-8 15-7 8 2 10 12 4 18Z"/><path d="M27 40 13 26c-4-4-3-10 2-12 4-1 8 1 12 6 4-5 8-7 12-6 5 2 6 8 2 12Z"/></svg>
  </div>
  <div class="icon-ring" style="left:653px;top:123px" aria-label="Remuneration icon">
    <svg viewBox="0 0 54 54"><rect x="8" y="12" width="38" height="32" rx="2"/><path d="M12 12V8h28v4"/><rect x="30" y="23" width="16" height="11"/><circle cx="36" cy="28.5" r="1.5"/></svg>
  </div>
  <div class="icon-ring" style="left:444px;top:383px" aria-label="Career growth icon">
    <svg viewBox="0 0 54 54"><path d="M6 6V48H48"/><path d="M12 44V34M18 44V26M24 44V30M30 44V20M36 44V24M42 44V14"/><path d="M10 38 22 26l8 6 16-18"/><path d="M38 13h8v8"/></svg>
  </div>
  <div class="icon-ring" style="left:56px;top:446px" aria-label="Diversity and inclusion icon">
    <svg viewBox="0 0 54 54"><path d="M27 8V44M17 44H37M12 14H42"/><circle cx="27" cy="8" r="2"/><path d="M12 14 6 28H18Z"/><path d="M42 14 36 28H48Z"/><path d="M6 28a6 5 0 0 0 12 0M36 28a6 5 0 0 0 12 0"/></svg>
  </div>
  <div class="icon-ring" style="left:454px;top:658px" aria-label="Recognition icon">
    <svg viewBox="0 0 54 54"><path d="M16 6H38V16L27 22 16 16Z"/><circle cx="27" cy="34" r="13"/><path d="M27 27l2.2 4.5 5 .7-3.6 3.5.9 5-4.5-2.4-4.5 2.4.9-5-3.6-3.5 5-.7Z"/></svg>
  </div>

  <section class="card" style="left:20px;top:150px;height:267px">
    <div class="card-ground" role="img" aria-label="Grounds pattern in grey, mint and peach"></div>
    <h2 class="card-head">Life Balance</h2>
    <ul class="card-list">
      <li>VELMAR Day Leave. An extra day off at Christmas</li>
      <li>BIRTHDAY Leave. A paid day off on your birthday</li>
      <li>A day off every month as Time In Lieu</li>
      <li>4 weeks Annual Leave</li>
      <li>Generous Personal Leave</li>
      <li>Support for parental leave for the birth or adoption of a child</li>
      <li>Flexible work arrangements</li>
    </ul>
  </section>

  <section class="card" style="left:216px;top:260px;height:235px">
    <div class="card-ground" role="img" aria-label="Grounds pattern in grey, mint and peach"></div>
    <h2 class="card-head">Wellbeing</h2>
    <ul class="card-list">
      <li>Up to $450 per year to spend on Wellbeing services such as gym or yoga memberships</li>
      <li>Free counselling services 24x7 via our Employee Assistance Program</li>
      <li>Discount private health insurance</li>
      <li>WHS policies which support a safe, inclusive work place</li>
    </ul>
  </section>

  <section class="card" style="left:415px;top:115px;height:233px">
    <div class="card-ground" role="img" aria-label="Grounds pattern in grey, mint and peach"></div>
    <h2 class="card-head">Career Growth &amp;Professional Development</h2>
    <ul class="card-list">
      <li>Ongoing internal training and development opportunities</li>
      <li>External study support @ study leave</li>
      <li>Access to the tools and technology to do your job well</li>
      <li>Career advancement opportunities</li>
      <li>Internal job vacancy listing</li>
    </ul>
  </section>

  <section class="card" style="left:615px;top:260px;height:205px">
    <div class="card-ground" role="img" aria-label="Grounds pattern in grey, mint and peach"></div>
    <h2 class="card-head">Remuneration &amp; Salary Packaging</h2>
    <ul class="card-list">
      <li>Competetive salary</li>
      <li>Ability to salary package up to $15,900 and reduce your tax. Package rent, home loans, child care and much more</li>
      <li>Salary package up to $2,650 on meal entertainment and holiday accommodation</li>
    </ul>
  </section>

  <section class="card" style="left:18px;top:585px;height:158px">
    <div class="card-ground" role="img" aria-label="Grounds pattern in grey, mint and peach"></div>
    <h2 class="card-head">Diversity &amp; Inclusion</h2>
    <ul class="card-list">
      <li>An inclusive and diverse culture where different backgrounds, experiences and perspectives are valued</li>
      <li>Gender diversity. Over 50% of our workforce and our leaders are female</li>
    </ul>
  </section>

  <section class="card" style="left:215px;top:523px;height:225px">
    <div class="card-ground" role="img" aria-label="Grounds pattern in grey, mint and peach"></div>
    <h2 class="card-head">Benefits</h2>
    <ul class="card-list">
      <li>Discounted vouchers for Harbor Grocers, Freshway, Sonic Depot, Cinemax Lane, Cellar Hall, ValueMart, Outland Gear and many others via Payline e-wallet</li>
      <li>A range of other employee discounts are also available, including access to discounted banking and finance, vehicle purchasing, leasing and hotel accomodation</li>
    </ul>
  </section>

  <section class="card" style="left:416px;top:527px;height:120px;width:178px">
    <div class="card-ground" role="img" aria-label="Grounds pattern in grey, mint and peach"></div>
    <h2 class="card-head">Recognition</h2>
    <ul class="card-list">
      <li>We celebrate our people for reaching service milestones</li>
      <li>Team &amp; individual recognition for high performance</li>
    </ul>
  </section>

  <section class="card" style="left:615px;top:495px;height:195px">
    <div class="card-ground" role="img" aria-label="Grounds pattern in grey, mint and peach"></div>
    <h2 class="card-head">Contributing to Community</h2>
    <ul class="card-list">
      <li>Team involvement in local charity and community events</li>
      <li>Participation in VELMAR's 1000 Jobs in 100 days</li>
      <li>Strong relationships and connection with Indigenous Communities in support of Indigenous Emplyment</li>
    </ul>
  </section>
</div>
</body>
</html>
```